RWT Fittings Ltd Business Cards

We need a business card with our business logo. We provide window and door installations on high-rises in west coast British Colombia, Canada.

I would like my business information and details on one side of the card, and the other side the company name with logo

Target Market(s)

General Contractors

Industry/Entity Type

Construction

Contact Information for Business Card

one side i want my company name and logo in the dark theme logo that i provided

Requirements
Must have
• Marco Peltieri, 16045518293, RWTFittings@mailbox-demo.com, 1407-5194 Linden Row Burnaby BC, V5H 2K9, Owner & Manager

```html
<!DOCTYPE html>
<html lang="en">
<head>
<meta charset="utf-8">
<title>RWT Fittings Ltd — Business Cards</title>
<link rel="stylesheet" href="https://fonts.googleapis.com/css2?family=Open+Sans:wght@400;600;700&display=swap">
<style>
  :root {
    --stage: #3a3a3a;
    --card: #1b1b1c;
    --blue: #29a9e1;
    --grey: #9a9a9a;
    --text: #ffffff;
  }
  * { margin: 0; padding: 0; box-sizing: border-box; }
  html, body {
    width: 1200px; height: 780px; overflow: hidden;
    background: var(--stage);
    font-family: "Open Sans", Arial, sans-serif;
  }
  .sheet {
    width: 1200px; height: 780px;
    display: flex; align-items: center; justify-content: center; gap: 40px;
  }
  .card {
    position: relative;
    width: 540px; height: 309px;
    background: var(--card);
    overflow: hidden;
    box-shadow: 0 12px 30px rgba(0,0,0,.45);
  }
  /* Contact side */
  .card-back__band {
    position: absolute; left: 0; bottom: 0; width: 540px; height: 309px;
  }
  .brand {
    display: flex; align-items: center; gap: 10px;
    color: var(--blue); font-weight: 700; white-space: nowrap;
  }
  .brand__mark { background: var(--blue); flex: none; }
  .card-back .brand {
    position: absolute; left: 28px; top: 80px; font-size: 21px;
  }
  .card-back .brand__mark { width: 20px; height: 20px; }
  .divider {
    position: absolute; left: 264px; top: 56px; width: 1px; height: 148px;
    background: var(--blue);
  }
  .contact {
    position: absolute; left: 282px; top: 54px; color: var(--text);
  }
  .contact__name {
    color: var(--blue); font-weight: 700; font-size: 20px;
    text-transform: uppercase; letter-spacing: .3px; line-height: 1.15;
  }
  .contact__role { font-size: 14px; margin-bottom: 8px; }
  .contact__line {
    display: flex; align-items: center; gap: 6px;
    font-size: 13px; line-height: 19px; white-space: nowrap;
  }
  .contact__line svg { width: 11px; height: 11px; flex: none; }
  .contact__address { font-size: 13px; line-height: 18px; margin-top: 4px; }
  /* Logo side */
  .card-front { display: flex; align-items: center; justify-content: center; }
  .card-front .brand { font-size: 40px; gap: 16px; }
  .card-front .brand__mark { width: 38px; height: 38px; }
</style>
</head>
<body>
<main class="sheet">
  <section class="card card-back" aria-label="Contact side">
    <svg class="card-back__band" viewBox="0 0 540 309" aria-hidden="true">
      <path d="M0 232 Q220 250 540 272 L540 276 Q230 258 0 240 Z" fill="var(--grey)"/>
      <path d="M0 252 Q240 264 540 262 L540 309 L0 309 Z" fill="var(--blue)"/>
    </svg>
    <div class="brand"><span class="brand__mark"></span>RWT Fittings Ltd</div>
    <div class="divider"></div>
    <div class="contact">
      <p class="contact__name">Marco Peltieri</p>
      <p class="contact__role">Owner &amp; Manager</p>
      <p class="contact__line">
        <svg viewBox="0 0 12 12"><path d="M2.5 1 L4.5 1 L5.3 3.5 L4 4.5 Q5 7 7.5 8 L8.5 6.7 L11 7.5 L11 9.5 Q10.5 11 9 11 Q1 10 1 3 Q1 1.5 2.5 1 Z" fill="var(--blue)"/></svg>
        16045518293
      </p>
      <p class="contact__line">
        <svg viewBox="0 0 12 12"><rect x="1" y="2.5" width="10" height="7" fill="var(--blue)"/><path d="M1 2.5 L6 6.5 L11 2.5" stroke="var(--card)" stroke-width="1" fill="none"/></svg>
        RWTFittings@mailbox-demo.com
      </p>
      <p class="contact__address">1407-5194 Linden Row<br>Burnaby BC, V5H 2K9</p>
    </div>
  </section>

  <section class="card card-front" aria-label="Logo side">
    <div class="brand"><span class="brand__mark"></span>RWT Fittings Ltd</div>
  </section>
</main>
</body>
</html>
```